UI Redesign For Mobile Events iPhone App

We need a new UI design for our Social Events mobile app. Our app called Vessa is geared to help users find trending events in their local area. We show visual metrics on percent full and male female ratio and age group ratings. We want people to see whats going on at event before they get there through our app. Also we have a group chat portion to our app that we need included in the design. We would like to see a fresh, clean, and easy to use user interface that uses colors like, purple, blue and or hot pink.You may visit our website myvessa.example for more information about what our app is geared to do.
Updates

Target Market(s)

Our target market people that use social networks and attend social events ranging from ages 16-44.

Industry/Entity Type

Events

Requirements
Must have
• We would like to see an Example layout of all screens. (UPDATE: Please use our current background in your design, A PSD has been uploaded for you to grab the background. The Vessa Logo is NOT required to be included at the top of every screen)

-Profile Screen: Shows points earned, events attending, events created
-Event Listings Screen: Must have large image for event, visual metrics, date& time, location, attend button, invite friends button, Label for user who created the event
-Event Description Page: Shows everything as the event listing, has a description of the event, shows friends that are attending, points available
-Group Messaging Screen
-Slide Out Navigation Screen
-Notification Screen
-Ticket Screen
-Friends Activity Screen
-Friends Profile View: Shows events they've attended and points they've earned under their contact picture; invite button
-Sign-In Screen
-Register Screen

A way to label/categorize our different types of events:
-Nightlife
-Family
-Live Music & Concerts
-Restaurants
Group Chat Layout
Visual Meters for Percent Full, Male Female Ratio, Age Rating

```html
<!DOCTYPE html>
<html lang="en">
<head>
<meta charset="utf-8">
<title>Vessa – Events App Screens</title>
<link href="https://fonts.googleapis.com/css2?family=Lato:wght@300;400;700&family=Roboto+Condensed:wght@400;700&display=swap" rel="stylesheet">
<style>
:root{
  --page:#f1e9ec;
  --ink:#ffffff;
  --night:#0b0710;
  --nav:#1b1222;
  --nav-line:#2c2236;
  --purple:#5b1fa0;
  --purple-bright:#6a28b8;
  --blue:#0a6cf0;
  --blue-dark:#1b3f93;
  --sky:#1a8ff0;
  --pink:#e0134f;
  --gold:#f4bf1a;
  --orange:#f07a12;
  --navy-text:#1f2a8c;
  --card:#ffffff;
  --glass:rgba(255,255,255,.55);
  --glass-line:rgba(255,255,255,.45);
  --label:rgba(10,8,20,.55);
}
*{box-sizing:border-box;margin:0;padding:0}
html,body{width:1200px;height:1000px;overflow:hidden}
body{background:radial-gradient(ellipse at 50% 50%,#f8f3f5 0%,var(--page) 100%);font-family:"Lato",Helvetica,Arial,sans-serif;color:var(--ink);position:relative}

.screen{position:absolute;width:256px;height:455px;overflow:hidden;background:var(--night)}
.bokeh{position:absolute;inset:0;
  background:
   radial-gradient(circle at 30% 12%,rgba(255,255,255,.55) 0,rgba(255,255,255,0) 18%),
   radial-gradient(circle at 75% 18%,rgba(255,130,220,.6) 0,rgba(255,130,220,0) 30%),
   radial-gradient(circle at 20% 30%,rgba(40,200,255,.75) 0,rgba(40,200,255,0) 38%),
   radial-gradient(circle at 85% 55%,rgba(200,120,255,.55) 0,rgba(200,120,255,0) 30%),
   radial-gradient(circle at 10% 65%,rgba(120,190,255,.45) 0,rgba(120,190,255,0) 30%),
   linear-gradient(180deg,#3a6a9a 0%,#2a3f7a 35%,#1a1530 70%,#07050b 100%);}
.status{position:absolute;top:0;left:0;right:0;height:18px;background:#000;font-size:8.5px;display:flex;align-items:center;justify-content:space-between;padding:0 5px;z-index:5}
.status .time{position:absolute;left:0;right:0;text-align:center;font-weight:700}
.topbar{position:absolute;top:18px;left:0;width:256px;height:40px;z-index:3}
.title{position:absolute;top:3px;left:0;right:0;text-align:center;font-weight:300;font-size:26px}
.icon-left{position:absolute;left:8px;top:10px}
.icon-right{position:absolute;right:8px;top:8px}

.bar{position:absolute;left:8px;width:240px;height:35px;display:flex;align-items:center;justify-content:center;font-size:14px}
.bar.half{width:117px}
.bar.right{left:131px}
.red{background:var(--pink)}
.blue{background:var(--blue)}
.violet{background:var(--purple)}

/* login */
.brand{position:absolute;top:80px;left:60px;display:flex;align-items:center;gap:10px}
.brand-dot{width:36px;height:36px;border-radius:50%;background:var(--purple-bright)}
.brand-name{font-weight:300;font-size:26px;letter-spacing:1px}
.field{position:absolute;left:8px;width:240px;height:35px;background:rgba(255,255,255,.78);color:#222;font-size:12px;padding:10px 14px;border-bottom:1px solid rgba(0,0,0,.08)}
.social{justify-content:flex-start;padding-left:60px}
.social.one{background:var(--blue-dark)}
.social.two{background:var(--sky)}

/* nav */
.nav{position:absolute;top:18px;left:0;width:145px;bottom:0;background:var(--nav);z-index:4}
.nav-item{height:45.5px;display:flex;align-items:center;gap:12px;padding-left:13px;font-size:12px;border-bottom:1px solid var(--nav-line);color:#e6e0ee}
.nav-item.active{background:var(--purple)}
.nav-item svg{width:18px;height:18px}
.peek{position:absolute;top:0;left:145px;width:256px;height:455px}

/* friends */
.dropdown{top:75px;justify-content:center;position:absolute}
.dropdown .chev{position:absolute;right:10px;top:10px}
.friends{position:absolute;left:8px;top:123px;width:240px;height:274px;background:rgba(220,225,235,.55)}
.friends-head{height:35px;border-bottom:1px solid var(--glass-line);display:flex;align-items:center;padding:0 10px;font-size:11px;color:#222;gap:18px;letter-spacing:.3px}
.friends-head .add{margin-left:auto;color:var(--blue);font-size:12px;display:flex;align-items:center;gap:5px}
.friend{position:absolute;width:50px;text-align:center;font-size:9.5px;color:#333}
.avatar{width:50px;height:50px;border-radius:50%;background:#1e1e1e;border:2px solid #fff;margin-bottom:1px}
.scroll{position:absolute;right:7px;top:48px;width:2px;height:210px;background:rgba(255,255,255,.5)}
.scroll::before{content:"";position:absolute;top:0;left:0;width:2px;height:85px;background:var(--purple-bright)}

/* events */
.event{position:absolute;left:8px;width:240px;background:var(--card);color:#111}
.tag{position:absolute;left:0;top:-7px;height:11px;padding:0 10px 0 4px;background:var(--gold);font-size:6px;line-height:11px;color:#fff;z-index:2;clip-path:polygon(0 0,100% 0,90% 100%,0 100%)}
.event-head{height:38px;padding:6px 40px 0 3px;position:relative;font-family:"Roboto Condensed",Arial,sans-serif}
.event-name{font-size:11.5px;color:var(--navy-text);line-height:12px;text-transform:uppercase}
.event-place{font-size:8px;font-weight:700;line-height:10px}
.event-date{font-size:6.5px;color:#333}
.price{position:absolute;right:0;top:0;width:36px;height:38px;border-left:1px solid #ddd;color:var(--pink);font-size:9px;display:flex;align-items:center;justify-content:center}
.photo{height:106px}
.photo.fest{background:linear-gradient(135deg,#d04a2a 0%,#e8b23a 35%,#6a8a3a 60%,#b8c4cc 100%)}
.photo.mall{background:linear-gradient(180deg,#9fc6e8 0%,#cfe0ec 35%,#3b6a32 65%,#6f7a72 100%)}
.event-foot{height:24px;display:flex;align-items:center;padding:0 3px;gap:4px;font-size:6px;color:#444;position:relative}
.join{color:var(--purple);font-size:6px;display:flex;align-items:center;gap:2px;width:34px}
.faces{display:flex;gap:1px}
.faces span{width:8px;height:8px;background:#8a98a8}
.foot-right{position:absolute;right:2px;top:2px;display:flex;align-items:center;gap:6px;font-size:7px;color:var(--navy-text)}

/* details */
.detail-head{height:24px;display:flex;align-items:center;justify-content:center;font-size:12px;color:var(--navy-text);font-family:"Roboto Condensed",Arial,sans-serif;padding-top:4px}
.info-row{position:absolute;left:8px;width:240px;height:25px;border-bottom:1px solid var(--glass-line);background:rgba(225,228,236,.55);font-size:8px;color:#222;display:flex;align-items:center;gap:10px;padding-left:10px}
.metrics{position:absolute;left:8px;top:333px;width:240px;height:60px;background:rgba(225,228,236,.55);display:flex;font-size:7.5px;color:#222}
.metric{flex:1;display:flex;flex-direction:column;align-items:center;justify-content:center;gap:1px}
.metric + .metric{border-left:1px solid rgba(255,255,255,.7)}

/* forms */
.form{position:absolute;left:8px;top:70px;width:240px;background:rgba(225,230,240,.5)}
.form-row{height:35px;display:flex;border-bottom:1px solid var(--glass-line)}
.form-row:last-child{border-bottom:0}
.form-label{width:44px;background:var(--label);font-size:8.5px;display:flex;align-items:center;justify-content:flex-end;padding-right:4px}
.form-value{font-size:9.5px;color:#222;display:flex;align-items:center;padding-left:5px}
.terms{position:absolute;top:340px;left:0;right:0;text-align:center;font-size:13px;text-decoration:underline}
</style>
</head>
<body>

<!-- Row 1 -->
<section class="screen" style="left:31px;top:33px" aria-label="Sign in screen">
  <div class="bokeh" role="img" aria-label="Blurred concert crowd with coloured stage lights"></div>
  <div class="status"><span>●●●○○ NOVA</span><span class="time">4:21 PM</span><span>100%</span></div>
  <div class="brand"><span class="brand-dot"></span><span class="brand-name">Vessa</span></div>
  <div class="field" style="top:170px">username</div>
  <div class="field" style="top:205px">password</div>
  <div class="bar half red" style="top:250px">Sign Up</div>
  <div class="bar half right blue" style="top:250px">Sign In</div>
  <div class="bar social one" style="top:329px">Log In with Linkly</div>
  <div class="bar social two" style="top:372px">Log In with Chirpa</div>
</section>

<section class="screen" style="left:324px;top:33px" aria-label="Slide out navigation over edit group">
  <div class="bokeh"></div>
  <div class="status"><span>●●●○○ NOVA</span><span class="time">4:21 PM</span><span>100%</span></div>
  <div class="peek">
    <div class="topbar">
      <svg class="icon-left" width="20" height="16" viewBox="0 0 20 16"><path d="M0 1h20M0 8h20M0 15h20" stroke="#fff" stroke-width="2"/></svg>
      <div class="title">Edit Vessa</div>
    </div>
    <div class="bar blue dropdown">Sloths</div>
    <div class="friends">
      <div class="friends-head">FRIENDS</div>
      <div class="friend" style="left:13px;top:48px"><div class="avatar"></div>user1</div>
      <div class="friend" style="left:86px;top:48px"><div class="avatar"></div>user1</div>
      <div class="friend" style="left:13px;top:120px"><div class="avatar"></div>user4</div>
      <div class="friend" style="left:86px;top:120px"><div class="avatar"></div>user5</div>
      <div class="friend" style="left:13px;top:192px"><div class="avatar"></div>user7</div>
      <div class="friend" style="left:86px;top:192px"><div class="avatar"></div>user8</div>
    </div>
    <div class="bar red" style="top:411px">Save</div>
  </div>
  <nav class="nav">
    <div class="nav-item"><svg viewBox="0 0 18 18"><circle cx="7" cy="6" r="3" fill="none" stroke="#fff"/><circle cx="12" cy="8" r="3" fill="none" stroke="#fff"/><path d="M2 16c0-4 8-4 8 0M8 16c0-3 8-3 8 0" fill="none" stroke="#fff"/></svg>Profile</div>
    <div class="nav-item"><svg viewBox="0 0 18 18"><rect x="1" y="4" width="16" height="11" fill="none" stroke="#fff"/><path d="M1 4l8 6 8-6" fill="none" stroke="#fff"/></svg>Messages</div>
    <div class="nav-item"><svg viewBox="0 0 18 18"><path d="M4 13V8a5 5 0 0110 0v5l2 1H2z M7 15a2 2 0 004 0" fill="none" stroke="#fff"/></svg>Notifications</div>
    <div class="nav-item active"><svg viewBox="0 0 18 18"><circle cx="9" cy="9" r="4" fill="none" stroke="#fff"/></svg>My Vessa</div>
    <div class="nav-item"><svg viewBox="0 0 18 18"><path d="M2 9l7-7h7v7l-7 7z" fill="none" stroke="#fff"/><circle cx="12.5" cy="5.5" r="1.2" fill="#fff"/></svg>Tickets</div>
    <div class="nav-item"><svg viewBox="0 0 18 18"><circle cx="9" cy="9" r="2.5" fill="none" stroke="#fff"/><g fill="#fff"><circle cx="9" cy="2.5" r="1.3"/><circle cx="9" cy="15.5" r="1.3"/><circle cx="2.5" cy="9" r="1.3"/><circle cx="15.5" cy="9" r="1.3"/><circle cx="4.4" cy="4.4" r="1.3"/><circle cx="13.6" cy="13.6" r="1.3"/><circle cx="13.6" cy="4.4" r="1.3"/><circle cx="4.4" cy="13.6" r="1.3"/></g></svg>Events</div>
  </nav>
</section>

<section class="screen" style="left:616px;top:33px" aria-label="Edit group screen">
  <div class="bokeh"></div>
  <div class="status"><span>●●●○○ NOVA</span><span class="time">4:21 PM</span><span>100%</span></div>
  <div class="topbar">
    <svg class="icon-left" width="20" height="16" viewBox="0 0 20 16"><path d="M0 1h20M0 8h20M0 15h20" stroke="#fff" stroke-width="2"/></svg>
    <div class="title">Edit Vessa</div>
  </div>
  <div class="bar blue dropdown">Sloths
    <svg class="chev" width="15" height="15" viewBox="0 0 15 15"><circle cx="7.5" cy="7.5" r="7" fill="#fff"/><path d="M4.5 6l3 3 3-3" fill="none" stroke="#0a6cf0" stroke-width="1.8"/></svg>
  </div>
  <div class="friends">
    <div class="friends-head">FRIENDS
      <svg width="16" height="16" viewBox="0 0 16 16" fill="#5b1fa0"><circle cx="2.5" cy="2.5" r="2"/><circle cx="8" cy="2.5" r="2"/><circle cx="13.5" cy="2.5" r="2"/><circle cx="2.5" cy="8" r="2"/><circle cx="8" cy="8" r="2"/><circle cx="13.5" cy="8" r="2"/><circle cx="2.5" cy="13.5" r="2"/><circle cx="8" cy="13.5" r="2"/><circle cx="13.5" cy="13.5" r="2"/></svg>
      <svg width="16" height="14" viewBox="0 0 16 14"><path d="M0 1h16M0 5h16M0 9h16M0 13h16" stroke="#111" stroke-width="1.5"/></svg>
      <span class="add"><svg width="14" height="14" viewBox="0 0 14 14"><circle cx="7" cy="7" r="7" fill="#0a6cf0"/><path d="M7 3.5v7M3.5 7h7" stroke="#fff" stroke-width="1.5"/></svg>Add</span>
    </div>
    <div class="friend" style="left:13px;top:48px"><div class="avatar"></div>user1</div>
    <div class="friend" style="left:86px;top:48px"><div class="avatar"></div>user1</div>
    <div class="friend" style="left:159px;top:48px"><div class="avatar"></div>user3</div>
    <div class="friend" style="left:13px;top:120px"><div class="avatar"></div>user4</div>
    <div class="friend" style="left:86px;top:120px"><div class="avatar"></div>user5</div>
    <div class="friend" style="left:159px;top:120px"><div class="avatar"></div>user6</div>
    <div class="friend" style="left:13px;top:192px"><div class="avatar"></div>user7</div>
    <div class="friend" style="left:86px;top:192px"><div class="avatar"></div>user8</div>
    <div class="friend" style="left:159px;top:192px"><div class="avatar"></div>user9</div>
    <div class="scroll"></div>
  </div>
  <div class="bar red" style="top:411px">Save</div>
</section>

<section class="screen" style="left:909px;top:33px" aria-label="Slide out navigation over events">
  <div class="bokeh"></div>
  <div class="status"><span>●●●○○ NOVA</span><span class="time">4:21 PM</span><span>100%</span></div>
  <div class="peek">
    <div class="topbar">
      <svg class="icon-left" width="20" height="16" viewBox="0 0 20 16"><path d="M0 1h20M0 8h20M0 15h20" stroke="#fff" stroke-width="2"/></svg>
      <div class="title">Events</div>
    </div>
    <article class="event" style="top:62px">
      <div class="tag">★ FEATURED</div>
      <div class="event-head"><div class="event-name">Harbor Lights Festival 2014</div><div class="event-place">Bayview City, Coastland</div><div class="event-date">Friday, 10Jan @ 8:0 AM</div></div>
      <div class="photo fest" role="img" aria-label="Street parade dancers in colourful costumes"></div>
      <div class="event-foot"><span class="join">♥ Unjoin</span></div>
      <div class="event-foot" style="height:14px;margin-top:-10px">You, Nikki &amp; Lex are joining</div>
    </article>
    <article class="event" style="top:250px">
      <div class="event-head"><div class="event-name">Maple Mall Summer Workshop</div><div class="event-place">Riverton City, Coastland</div><div class="event-date">Tuesday, 01April @ 8:0 AM</div></div>
      <div class="photo mall" role="img" aria-label="Shopping mall exterior beside a tree-lined road"></div>
      <div class="event-foot"><span class="join" style="color:#888">♥ Join</span></div>
    </article>
    <article class="event" style="top:428px">
      <div class="event-head"><div class="event-name">Summer Photography Contest</div></div>
    </article>
  </div>
  <nav class="nav">
    <div class="nav-item"><svg viewBox="0 0 18 18"><circle cx="7" cy="6" r="3" fill="none" stroke="#fff"/><circle cx="12" cy="8" r="3" fill="none" stroke="#fff"/><path d="M2 16c0-4 8-4 8 0M8 16c0-3 8-3 8 0" fill="none" stroke="#fff"/></svg>Profile</div>
    <div class="nav-item"><svg viewBox="0 0 18 18"><rect x="1" y="4" width="16" height="11" fill="none" stroke="#fff"/><path d="M1 4l8 6 8-6" fill="none" stroke="#fff"/></svg>Messages</div>
    <div class="nav-item"><svg viewBox="0 0 18 18"><path d="M4 13V8a5 5 0 0110 0v5l2 1H2z M7 15a2 2 0 004 0" fill="none" stroke="#fff"/></svg>Notifications</div>
    <div class="nav-item"><svg viewBox="0 0 18 18"><circle cx="9" cy="9" r="4" fill="none" stroke="#fff"/></svg>My Vessa</div>
    <div class="nav-item"><svg viewBox="0 0 18 18"><path d="M2 9l7-7h7v7l-7 7z" fill="none" stroke="#fff"/><circle cx="12.5" cy="5.5" r="1.2" fill="#fff"/></svg>Tickets</div>
    <div class="nav-item active"><svg viewBox="0 0 18 18"><circle cx="9" cy="9" r="2.5" fill="none" stroke="#fff"/><g fill="#fff"><circle cx="9" cy="2.5" r="1.3"/><circle cx="9" cy="15.5" r="1.3"/><circle cx="2.5" cy="9" r="1.3"/><circle cx="15.5" cy="9" r="1.3"/><circle cx="4.4" cy="4.4" r="1.3"/><circle cx="13.6" cy="13.6" r="1.3"/><circle cx="13.6" cy="4.4" r="1.3"/><circle cx="4.4" cy="13.6" r="1.3"/></g></svg>Events</div>
  </nav>
</section>

<!-- Row 2 -->
<section class="screen" style="left:31px;top:518px" aria-label="Event listings screen">
  <div class="bokeh"></div>
  <div class="status"><span>●●●○○ NOVA</span><span class="time">4:21 PM</span><span>100%</span></div>
  <div class="topbar">
    <svg class="icon-left" width="20" height="16" viewBox="0 0 20 16"><path d="M0 1h20M0 8h20M0 15h20" stroke="#fff" stroke-width="2"/></svg>
    <div class="title">Events</div>
    <svg class="icon-right" width="22" height="22" viewBox="0 0 22 22"><path d="M11 0v22M0 11h22" stroke="#fff" stroke-width="2"/></svg>
  </div>
  <article class="event" style="top:62px">
    <div class="tag">★ FEATURED</div>
    <div class="event-head"><div class="event-name">Harbor Lights Festival 2014</div><div class="event-place">Bayview City, Coastland</div><div class="event-date">Friday, 10Jan @ 8:0 AM</div><div class="price">Free</div></div>
    <div class="photo fest" role="img" aria-label="Street parade dancers in colourful costumes"></div>
    <div class="event-foot">
      <div><div class="join">♥ Unjoin</div><div style="display:flex;gap:3px;align-items:center"><span class="faces"><span></span><span></span><span></span></span>You, Nikki &amp; Lex are joining</div></div>
      <div class="foot-right">
        <svg width="20" height="20" viewBox="0 0 20 20"><circle cx="10" cy="10" r="8" fill="none" stroke="#ddd" stroke-width="2.5"/><circle cx="10" cy="10" r="8" fill="none" stroke="#f07a12" stroke-width="2.5" stroke-dasharray="37.7 50.3" transform="rotate(-90 10 10)"/><text x="10" y="12" font-size="5.5" text-anchor="middle" fill="#333">75%</text></svg>
        <span style="margin-left:14px">M/F Ratio</span>
        <svg width="20" height="20" viewBox="0 0 20 20"><path d="M10 0a10 10 0 000 20z" fill="#0a6cf0"/><path d="M10 0a10 10 0 010 20z" fill="#ff1a8c"/></svg>
      </div>
    </div>
  </article>
  <article class="event" style="top:250px">
    <div class="event-head"><div class="event-name">Maple Mall Summer Workshop</div><div class="event-place">Riverton City, Coastland</div><div class="event-date">Tuesday, 01April @ 8:0 AM</div><div class="price">$20</div></div>
    <div class="photo mall" role="img" aria-label="Shopping mall exterior beside a tree-lined road"></div>
    <div class="event-foot">
      <div><div class="join" style="color:#888">♥ Join</div><div style="display:flex;gap:3px;align-items:center"><span class="faces"><span></span></span>B-ann is joining</div></div>
      <div class="foot-right">
        <svg width="20" height="20" viewBox="0 0 20 20"><circle cx="10" cy="10" r="8" fill="none" stroke="#ddd" stroke-width="2.5"/><circle cx="10" cy="10" r="8" fill="none" stroke="#f07a12" stroke-width="2.5" stroke-dasharray="37.7 50.3" transform="rotate(-90 10 10)"/><text x="10" y="12" font-size="5.5" text-anchor="middle" fill="#333">75%</text></svg>
        <span style="margin-left:14px">M/F Ratio</span>
        <svg width="20" height="20" viewBox="0 0 20 20"><path d="M10 0a10 10 0 000 20z" fill="#0a6cf0"/><path d="M10 0a10 10 0 010 20z" fill="#ff1a8c"/></svg>
      </div>
    </div>
  </article>
  <article class="event" style="top:428px">
    <div class="event-head"><div class="event-name">Summer Photography Contest</div><div class="event-place">Hillcrest, Northvale, Coastland</div><div class="price">$25</div></div>
  </article>
</section>

<section class="screen" style="left:324px;top:518px" aria-label="Event details screen">
  <div class="bokeh"></div>
  <div class="status"><span>●●●○○ NOVA</span><span class="time">4:21 PM</span><span>100%</span></div>
  <div class="topbar">
    <svg class="icon-left" width="20" height="16" viewBox="0 0 20 16"><path d="M20 8H1M8 1L1 8l7 7" fill="none" stroke="#fff" stroke-width="1.8"/></svg>
    <div class="title">Details</div>
    <svg class="icon-right" width="22" height="22" viewBox="0 0 22 22"><path d="M11 0v22M0 11h22" stroke="#fff" stroke-width="2"/></svg>
  </div>
  <article class="event" style="top:62px">
    <div class="tag">★ FEATURED</div>
    <div class="detail-head">HARBOR LIGHTS FESTIVAL 2014</div>
    <div class="photo fest" role="img" aria-label="Street parade dancers in colourful costumes" style="height:100px"></div>
    <div class="event-foot" style="height:22px"><span class="join" style="width:40px">♥ Unjoin</span><span class="faces"><span></span><span></span><span></span></span>You, Nikki &amp; Lex are joining</div>
  </article>
  <div class="info-row" style="top:233px"><svg width="9" height="12" viewBox="0 0 9 12"><path d="M4.5 12S0 7 0 4.5a4.5 4.5 0 019 0C9 7 4.5 12 4.5 12z" fill="#fff"/><circle cx="4.5" cy="4.5" r="1.6" fill="#8890a8"/></svg>Bayview City, Coastland</div>
  <div class="info-row" style="top:258px"><svg width="11" height="10" viewBox="0 0 11 10"><rect x=".5" y="1" width="10" height="8.5" fill="none" stroke="#fff"/><path d="M.5 3.5h10" stroke="#fff"/></svg>Friday, 10Jan @ 8:0 AM</div>
  <div class="info-row" style="top:283px"><svg width="11" height="11" viewBox="0 0 11 11"><path d="M0 5.5L5.5 0H11v5.5L5.5 11z" fill="#fff"/><circle cx="8" cy="3" r="1" fill="#8890a8"/></svg>FREE</div>
  <div class="info-row" style="top:308px"><svg width="11" height="11" viewBox="0 0 11 11"><path d="M5.5 0l1.6 3.6 3.9.4-2.9 2.6.8 3.9-3.4-2-3.4 2 .8-3.9L0 4l3.9-.4z" fill="#fff"/></svg>Everything is free</div>
  <div class="metrics">
    <div class="metric">
      <svg width="38" height="38" viewBox="0 0 38 38"><circle cx="19" cy="19" r="15" fill="none" stroke="#fff" stroke-width="4"/><circle cx="19" cy="19" r="15" fill="none" stroke="#f07a12" stroke-width="4" stroke-dasharray="70.7 94.2" transform="rotate(-90 19 19)"/><text x="19" y="22" font-size="9" text-anchor="middle" fill="#222" font-family="Lato,sans-serif">75%</text></svg>
      Percentage
    </div>
    <div class="metric">
      <svg width="36" height="36" viewBox="0 0 36 36"><path d="M18 0a18 18 0 000 36z" fill="#0a6cf0"/><path d="M18 0a18 18 0 010 36z" fill="#ff1a8c"/></svg>
      M/F Ratio
    </div>
  </div>
  <div class="bar half red" style="top:411px"><svg width="24" height="14" viewBox="0 0 24 14"><path d="M24 7H1M7 1L1 7l6 6" fill="none" stroke="#fff" stroke-width="1.6"/></svg></div>
  <div class="bar half right blue" style="top:411px"><svg width="24" height="14" viewBox="0 0 24 14"><path d="M0 7h23M17 1l6 6-6 6" fill="none" stroke="#fff" stroke-width="1.6"/></svg></div>
</section>

<section class="screen" style="left:616px;top:518px" aria-label="Create event screen">
  <div class="bokeh"></div>
  <div class="status"><span>●●●○○ NOVA</span><span class="time">4:21 PM</span><span>100%</span></div>
  <div class="topbar">
    <svg class="icon-left" width="20" height="16" viewBox="0 0 20 16"><path d="M20 8H1M8 1L1 8l7 7" fill="none" stroke="#fff" stroke-width="1.8"/></svg>
    <div class="title">Create Event</div>
    <svg class="icon-right" width="18" height="18" viewBox="0 0 18 18" style="top:11px"><path d="M1 1l16 16M17 1L1 17" stroke="#fff" stroke-width="1.8"/></svg>
  </div>
  <div class="form">
    <div class="form-row"><div class="form-label">Name:</div></div>
    <div class="form-row"><div class="form-label">Where:</div></div>
    <div class="form-row"><div class="form-label">When:</div></div>
    <div class="form-row"><div class="form-label">Cost:</div></div>
    <div class="form-row"><div class="form-label">Special:</div></div>
  </div>
  <div class="bar violet" style="top:262px;gap:8px"><svg width="20" height="16" viewBox="0 0 20 16"><rect x=".75" y=".75" width="18.5" height="14.5" fill="none" stroke="#fff" stroke-width="1.5"/><path d="M3 13l5-5 3 3 2-2 4 4z" fill="#fff"/><circle cx="14" cy="5" r="1.5" fill="#fff"/></svg>Upload Event Photo</div>
  <div class="terms">Terms of Agreements</div>
  <div class="bar red" style="top:411px">Create Event</div>
</section>

<section class="screen" style="left:909px;top:518px" aria-label="Ticket screen">
  <div class="bokeh"></div>
  <div class="status"><span>●●●○○ NOVA</span><span class="time">4:21 PM</span><span>100%</span></div>
  <div class="topbar">
    <svg class="icon-left" width="20" height="16" viewBox="0 0 20 16"><path d="M0 1h20M0 8h20M0 15h20" stroke="#fff" stroke-width="2"/></svg>
    <div class="title">Tickets</div>
  </div>
  <div class="form">
    <div class="form-row"><div class="form-label">Event:</div><div class="form-value">Harbor Lights Festival 2014</div></div>
    <div class="form-row"><div class="form-label">Where:</div><div class="form-value">Bayview City, Coastland</div></div>
    <div class="form-row"><div class="form-label">When:</div><div class="form-value">Friday, 10Jan @ 8:0 AM</div></div>
    <div class="form-row"><div class="form-label">Pin:</div><div class="form-value">0123456</div></div>
    <div class="form-row"><div class="form-label">Type:</div><div class="form-value">Free</div></div>
  </div>
  <div class="bar violet" style="top:262px">Go To Event</div>
  <div class="bar half red" style="top:411px"><svg width="24" height="14" viewBox="0 0 24 14"><path d="M24 7H1M7 1L1 7l6 6" fill="none" stroke="#fff" stroke-width="1.6"/></svg></div>
  <div class="bar half right blue" style="top:411px"><svg width="24" height="14" viewBox="0 0 24 14"><path d="M0 7h23M17 1l6 6-6 6" fill="none" stroke="#fff" stroke-width="1.6"/></svg></div>
</section>

</body>
</html>
```